Supplement Company needs final product mockups and label design

We're a Supplement company launching 4 Hydration Supplement flavours. We need someone to re create the EXACT design with what ChatGPT has already generated and tweak the design slightly so that spelling is correct and callout icons are designed. We then also need someone to do the back of label design that includes space for the barcode, nutrition table, blurb etc. Bonus if you have experience with PLDMQ compliance regulations and designing supplement labels.

We want the other 3 flavours (Lime, Mango & Watermelon) to match the design of the strawberry flavour including details like all the callout icons on the left side of the front, the word "electrolytes" in the dark coloured box, the words "hydration powder" just above the callout icons. Please re - design the callout icons to better suit the callout.

I've also attached an image of what the nutrition label should look like.

Please include the Following on the back of the label:
"Directions: Mix 1 Scoop with 400-500ml of water & Mix well before drinking. Do not exceed 2 servings per day.

Why rest when you can KORVA?
Your body wasn’t made to run on sugar, chemicals, and artificial junk — and your hydration shouldn’t either. At KORVA Nutrition, we’ve created a clean, mineral-rich formula with Brindlemoor Flakes and essential electrolytes to fuel you the right way. No toxins, no fillers — just real ingredients that work with your body, not against it.
Drink the way earth designed. Stay pure. KORVA.

AUSTRALIAN OWNED AND MADE

Store in a cool, dry place below 30°C. Reseal after use"

Product Formula & Ingredients:

* Sodium (Sea Salt, Brindlemoor Flakes®, Himalayan Pink Salt): 1000 mg
* Potassium (from Potassium Chloride): 200 mg
* Magnesium (from Magnesium Glycinate): 60 mg
* Total Carbohydrates: 0 g
* Sugars: 0 g
* Calories: 1 kcal

Ingredients:
Sea Salt, Citric Acid, Brindlemoor Flakes®, Himalayan Pink Salt, Potassium Chloride, Magnesium Glycinate, Natural Flavour (e.g. Mango), Stevia Leaf Extract.
Updates

I would like to give designers more time to closely replicate what I have included in the brief and make sure they can create something very beautifully

Industry/Entity Type

Supplements

Font styles to use
Other font styles liked:
• Montserrat

Requirements
Must have
• Back of label design aswell and Australian Nutrition table
Nice to have
• Design as close to the Provided images as possible
Should not have
• Should not be too different to the attached images

```html
<!DOCTYPE html>
<html lang="en">
<head>
<meta charset="utf-8">
<title>KORVA Nutrition – Watermelon Electrolytes Label</title>
<link rel="stylesheet" href="https://fonts.googleapis.com/css2?family=Anton&family=Montserrat:wght@500;600;700;800;900&display=swap">
<style>
  :root{
    --label-red:#e8305f;
    --label-red-deep:#d81f4f;
    --label-pink:#f0487a;
    --ink-white:#ffffff;
    --pill-black:#111111;
    --melon-green:#3f9a3a;
    --melon-flesh:#ef4b4f;
  }
  *{box-sizing:border-box;margin:0;padding:0}
  html,body{width:802px;height:1200px;overflow:hidden}
  body{background:var(--label-red);font-family:"Montserrat",sans-serif;color:var(--ink-white)}
  .label{
    position:relative;width:802px;height:1200px;overflow:hidden;
    background:radial-gradient(ellipse at 50% 18%, var(--label-pink) 0%, var(--label-red) 45%, var(--label-red-deep) 100%);
  }
  .brand{position:absolute;top:70px;left:0;right:0;text-align:center;font-weight:800}
  .brand-name{font-size:118px;line-height:1;letter-spacing:2px}
  .brand-sub{font-size:30px;letter-spacing:13px;margin-top:6px;padding-left:13px}
  .flavour{
    position:absolute;top:266px;left:30px;right:30px;text-align:center;
    font-family:"Anton",sans-serif;font-weight:400;font-size:138px;line-height:1;letter-spacing:0;
    white-space:nowrap;transform:scaleY(1.22);transform-origin:50% 0;
    text-shadow:0 4px 6px rgba(0,0,0,.25);
  }
  .pill{
    position:absolute;top:470px;left:38px;right:38px;height:96px;border-radius:48px;
    background:var(--pill-black);display:flex;align-items:center;justify-content:center;
    font-weight:800;font-size:60px;letter-spacing:7px;padding-left:7px;
  }
  .product-type{position:absolute;top:612px;left:40px;font-weight:600;font-size:38px;line-height:1.15;letter-spacing:-0.5px}
  .callouts{position:absolute;top:724px;left:40px;list-style:none}
  .callout{display:flex;align-items:center;gap:14px;height:92px}
  .callout svg{width:48px;height:48px;flex:none}
  .callout span{font-weight:500;font-size:26px;line-height:1.08;letter-spacing:-1px}
  .artwork{
    position:absolute;top:640px;left:280px;width:490px;height:430px;border-radius:46% 50% 40% 44%;
    background:radial-gradient(ellipse at 70% 45%, var(--melon-green) 0%, #5aa84a 40%, var(--melon-flesh) 75%, rgba(239,75,79,0) 100%);
  }
  .net-weight{position:absolute;top:1112px;left:0;right:0;text-align:center;font-weight:800;font-size:44px}
</style>
</head>
<body>
<main class="label">
  <header class="brand">
    <div class="brand-name">KORVA</div>
    <div class="brand-sub">NUTRITION</div>
  </header>

  <h1 class="flavour">WATERMELON</h1>
  <div class="pill">ELECTROLYTES</div>

  <p class="product-type">HYDRATION<br>POWDER</p>

  <ul class="callouts">
    <li class="callout">
      <svg viewBox="0 0 48 48" fill="none" stroke="#fff" stroke-width="2"><circle cx="24" cy="24" r="22"/><circle cx="24" cy="18" r="6"/><path d="M14 36c2-7 18-7 20 0"/></svg>
      <span>KID<br>FRIENDLY</span>
    </li>
    <li class="callout">
      <svg viewBox="0 0 48 48" fill="none" stroke="#fff" stroke-width="2"><circle cx="24" cy="24" r="22"/><rect x="15" y="15" width="9" height="9"/><rect x="24" y="24" width="9" height="9"/><path d="M12 12l24 24"/></svg>
      <span>SUGAR<br>FREE</span>
    </li>
    <li class="callout">
      <svg viewBox="0 0 48 48" fill="none" stroke="#fff" stroke-width="2"><circle cx="24" cy="24" r="22"/><path d="M24 34c-8-5-11-9-11-13a5 5 0 0 1 11-2 5 5 0 0 1 11 2c0 4-3 8-11 13z"/></svg>
      <span>PALEO<br>FRIENDLY</span>
    </li>
    <li class="callout">
      <svg viewBox="0 0 48 48" fill="none" stroke="#fff" stroke-width="2"><circle cx="24" cy="24" r="22"/><path d="M24 12v26M24 18l-5-4M24 18l5-4M24 25l-5-4M24 25l5-4M24 32l-5-4M24 32l5-4"/></svg>
      <span>GLUTEN<br>FREE</span>
    </li>
  </ul>

  <div class="artwork" role="img" aria-label="Illustration of a whole watermelon with a cut slice"></div>

  <p class="net-weight">NET WT. 180g</p>
</main>
</body>
</html>
```